Brellwick Partners, LLC Stationary

Brellwick Partners, LLC is a new financial planning and consulting company. We are looking for designs on business cards, letterhead, envelopes, and anything else that would be useful. Our preference for business card design is two sided. We are looking for a professional and clean look with incorporating the logo and patriotic feel. Thank you to all who participate and good luck!

```html
<!DOCTYPE html>
<html lang="en">
<head>
<meta charset="utf-8">
<title>Brellwick Partners, LLC — Business Card</title>
<link href="https://fonts.googleapis.com/css2?family=Montserrat:wght@400;600;700&family=Open+Sans:wght@400;600&display=swap" rel="stylesheet">
<style>
  :root {
    --navy: #123c6b;
    --navy-band: #2b5683;
    --red: #c8232c;
    --white: #ffffff;
    --ink: #3c3c3c;
    --page: #e9e6e1;
  }
  * { margin: 0; padding: 0; box-sizing: border-box; }
  html, body { width: 1200px; height: 950px; overflow: hidden; background: var(--page); }
  .sheet {
    position: relative; width: 1200px; height: 950px;
    display: flex; align-items: center; justify-content: center; gap: 60px;
  }
  .card {
    position: relative; width: 520px; height: 297px;
    box-shadow: 0 8px 22px rgba(0,0,0,.18);
    overflow: hidden;
  }
  /* Front */
  .card-front { background: var(--white); }
  .name-band {
    position: absolute; left: 0; top: 96px; width: 300px; height: 70px;
    background: linear-gradient(90deg, var(--navy) 0%, var(--navy-band) 100%);
    clip-path: polygon(0 0, 100% 0, 88% 100%, 0 100%);
    padding: 14px 0 0 26px; color: var(--white);
  }
  .person-name {
    font-family: "Montserrat", sans-serif; font-weight: 700; font-size: 19px;
    letter-spacing: .5px; text-transform: uppercase; font-variant: small-caps;
  }
  .person-title {
    font-family: "Open Sans", sans-serif; font-size: 12px; letter-spacing: 1.5px;
    text-transform: uppercase; margin-top: 4px; opacity: .9;
  }
  .brand {
    position: absolute; left: 300px; top: 98px; display: flex; align-items: center; gap: 10px;
  }
  .brand-mark { width: 16px; height: 16px; background: var(--red); }
  .brand-name {
    font-family: "Montserrat", sans-serif; font-weight: 600; font-size: 17px;
    color: var(--navy); letter-spacing: .5px; line-height: 1.15;
  }
  .brand-tagline {
    position: absolute; left: 326px; top: 146px;
    font-family: "Open Sans", sans-serif; font-size: 8px; color: var(--ink);
    letter-spacing: 1px; text-transform: uppercase;
  }
  .contact-list {
    position: absolute; left: 26px; bottom: 24px; list-style: none;
    font-family: "Open Sans", sans-serif; font-size: 12px; color: var(--ink);
  }
  .contact-list li { display: flex; align-items: center; gap: 8px; line-height: 19px; }
  .contact-list svg { width: 11px; height: 11px; fill: var(--navy); }
  .address {
    position: absolute; right: 26px; bottom: 24px; text-align: right;
    font-family: "Open Sans", sans-serif; font-size: 12px; color: var(--ink); line-height: 19px;
  }
  /* Back */
  .card-back {
    background: var(--navy); color: var(--white);
    display: flex; flex-direction: column; align-items: center; justify-content: center; gap: 10px;
  }
  .back-brand { display: flex; align-items: center; gap: 14px; }
  .back-brand .brand-mark { width: 26px; height: 26px; }
  .back-brand-name {
    font-family: "Montserrat", sans-serif; font-weight: 600; font-size: 30px; letter-spacing: 1px;
  }
  .back-tagline {
    font-family: "Open Sans", sans-serif; font-size: 10px; letter-spacing: 2px; text-transform: uppercase;
  }
  .back-web { font-family: "Open Sans", sans-serif; font-size: 13px; letter-spacing: 3px; opacity: .9; }
</style>
</head>
<body>
<main class="sheet">
  <section class="card card-front" aria-label="Business card front">
    <div class="name-band">
      <p class="person-name">Daniel Harlow</p>
      <p class="person-title">CEO / Founder</p>
    </div>
    <div class="brand">
      <span class="brand-mark"></span>
      <span class="brand-name">Brellwick Partners, LLC</span>
    </div>
    <p class="brand-tagline">Financial Planning and Consulting</p>
    <ul class="contact-list">
      <li><svg viewBox="0 0 12 12"><path d="M2.5 0.5l2 2-1 1.5c.6 1.5 2 2.9 3.5 3.5l1.5-1 2 2-1.2 1.8C5 9.8 2.2 7 0.7 1.7z"/></svg>555 210 4837</li>
      <li><svg viewBox="0 0 12 12"><rect x="1" y="4" width="10" height="7" rx="1"/><rect x="3" y="0.5" width="6" height="4"/></svg>555 392 7165</li>
      <li><svg viewBox="0 0 12 12"><path d="M0.5 2h11v8h-11z M1 2.5l5 4 5-4" fill="none" stroke="#123c6b" stroke-width="1.2"/></svg>daniel@brellwick.com</li>
      <li><svg viewBox="0 0 12 12"><circle cx="6" cy="6" r="5.3" fill="none" stroke="#123c6b" stroke-width="1.2"/><path d="M0.7 6h10.6M6 0.7c-3 3-3 7.6 0 10.6M6 0.7c3 3 3 7.6 0 10.6" fill="none" stroke="#123c6b" stroke-width="1"/></svg>www.brellwick.com</li>
    </ul>
    <p class="address">214 Larchmont Way<br>Fairview, Oregon 97024</p>
  </section>

  <section class="card card-back" aria-label="Business card back">
    <div class="back-brand">
      <span class="brand-mark"></span>
      <span class="back-brand-name">Brellwick Partners, LLC</span>
    </div>
    <p class="back-tagline">Financial Planning and Consulting</p>
    <p class="back-web">www.brellwick.com</p>
  </section>
</main>
</body>
</html>
```